Business Card Design for Bright Pebble

Bright Pebble is a company which caters to children .We provide clothes, shoes,kids furniture,room accessories,school bags,lunch boxes ,stationary etc for children ages 3-13.

Industry/Entity Type

Business

Contact Information for Business Card

Adetutu Ekanemi
CEO Bright Pebble
+2347051926384, +2348062417390
www.brightpebbleng.example
Instagram: brightpebbleng

Requirements
Must have
• Playful and colourful design.playful ,colourful text as well.
Nice to have
• Cartoon like drawings or graphics of happy,playful kids.

```html
<!DOCTYPE html>
<html lang="en">
<head>
<meta charset="utf-8">
<title>Bright Pebble – Business Card</title>
<link rel="stylesheet" href="https://fonts.googleapis.com/css2?family=Open+Sans:wght@400;600;700&display=swap">
<style>
  :root {
    --page: #ffffff;
    --card: #ffffff;
    --card-edge: #d9d9d9;
    --ink: #3a3a3a;
    --ink-soft: #555555;
    --kid-pink: #e2327f;
    --kid-yellow: #f6d21c;
    --kid-blue: #2a8fd8;
    --kid-orange: #f08a2c;
    --kid-red: #e0312f;
    --kid-green: #5fae2e;
    --kid-purple: #9a4fa0;
  }
  * { margin: 0; padding: 0; box-sizing: border-box; }
  html, body {
    width: 1200px;
    height: 1200px;
    overflow: hidden;
    background: var(--page);
    font-family: "Open Sans", Arial, sans-serif;
    color: var(--ink);
  }
  .business-card {
    position: absolute;
    left: 301px;
    top: 404px;
    width: 596px;
    height: 384px;
    background: var(--card);
    border: 1px solid var(--card-edge);
    overflow: hidden;
  }
  .kids-ring {
    position: absolute;
    left: -8px;
    top: -14px;
    width: 220px;
    height: 220px;
    border-radius: 50%;
    background: conic-gradient(
      var(--kid-red), var(--kid-yellow), var(--kid-blue), var(--kid-orange),
      var(--kid-yellow), var(--kid-red), var(--kid-blue), var(--kid-pink),
      var(--kid-green), var(--kid-purple), var(--kid-red));
    opacity: 0.55;
    -webkit-mask: radial-gradient(circle, transparent 56%, #000 60%, #000 96%, transparent 100%);
            mask: radial-gradient(circle, transparent 56%, #000 60%, #000 96%, transparent 100%);
  }
  .brand-name {
    position: absolute;
    left: 97px;
    top: 90px;
    transform: translate(-50%, -50%);
    font-size: 17px;
    font-weight: 700;
    color: var(--kid-pink);
    white-space: nowrap;
  }
  .contact-block {
    position: absolute;
    right: 49px;
    top: 140px;
    text-align: right;
    line-height: 1.2;
  }
  .person-name { font-size: 14.5px; font-weight: 400; color: var(--kid-blue); }
  .company { font-size: 11.5px; font-weight: 700; color: var(--kid-orange); }
  .phones { margin-top: 14px; font-size: 9.5px; color: var(--kid-green); }
  .phone { display: flex; justify-content: flex-end; align-items: center; gap: 3px; }
  .phone-icon { width: 7px; height: 7px; }
  .phone-icon path { fill: var(--kid-green); }
  .web { margin-top: 10px; font-size: 13px; font-weight: 700; color: var(--kid-purple); }
  .social { font-size: 11px; color: var(--kid-red); }
</style>
</head>
<body>
  <div class="business-card">
    <div class="kids-ring" role="img" aria-label="Ring of colourful cartoon children holding hands"></div>
    <div class="brand-name">Bright Pebble</div>

    <div class="contact-block">
      <div class="person-name">Adetutu Ekanemi CEO</div>
      <div class="company">Bright Pebble</div>
      <div class="phones">
        <div class="phone">
          <svg class="phone-icon" viewBox="0 0 10 10" aria-hidden="true"><path d="M2 1 L4 1 L4.5 3 L3.3 3.8 Q4.2 5.8 6.2 6.7 L7 5.5 L9 6 L9 8 Q5 9.5 1.5 5 Q0.5 3 2 1 Z"/></svg>
          <span>+ 234 705 192 6384</span>
        </div>
        <div class="phone">
          <svg class="phone-icon" viewBox="0 0 10 10" aria-hidden="true"><path d="M2 1 L4 1 L4.5 3 L3.3 3.8 Q4.2 5.8 6.2 6.7 L7 5.5 L9 6 L9 8 Q5 9.5 1.5 5 Q0.5 3 2 1 Z"/></svg>
          <span>+ 234 806 241 7390</span>
        </div>
      </div>
      <div class="web">www.brightpebbleng.example</div>
      <div class="social">Instagram.brightpebbleng</div>
    </div>
  </div>
</body>
</html>
```